Federal IT Consulting Company - Brisolux Consulting Group

We're seeking a skilled web designer to create a modern, bold, and engaging WordPress website for Brisolux Consulting Group, LLC. Our company specializes in federal IT consulting, and our name is a play on "Brightening Solutions." The website should reflect our expertise in the federal technology marketplace and position us as a trusted partner for clients navigating their IT journey.

contact: info@brisoluxgrp-example.com

Current Status

WordPress is already installed on our hosting account
We have an existing logo (may need modernization)

Design Requirements

Style:

Modern and visually striking design
Bold elements to convey confidence and expertise
Incorporate the concept of "brightening solutions" into the design

Features:

Modern UX sliders for dynamic content presentation
Eye-catching, high-quality images (stock photos to be sourced by the designer)
Responsive design for all devices

Color Scheme:

To be proposed by the designer, should align with our brand and convey trust and technological expertise

Logo:

Evaluate our current logo
Create a transparent background version if needed
Propose modernization if deemed necessary

Accessibility:

Ensure design elements are accessible to users with disabilities
Use high contrast ratios for text and background colors
Provide text alternatives for non-text content

Website Structure
Create the following pages, with the possibility of subpages:

Home
Services
About
Contact

Specific Page Requirements
Home Page

Striking hero section with a clear value proposition
Overview of our services
Client testimonials or trust indicators

Services Page

Detailed list of our IT consulting services
Clear explanation of how we help navigate the federal IT landscape

About Page

Company history and mission
Team highlights (if applicable)
Our approach to federal IT consulting

Contact Page

Contact form
Other contact methods (phone, email)

Technical Requirements

Fully responsive design
SEO best practices implemented
Fast loading times
Integration with necessary plugins (to be discussed)
Training on how to update and maintain the site
Full compliance with Web Content Accessibility Guidelines (WCAG) 2.1 Level AA
Adherence to Section 508 standards for federal website accessibility
Implementation of necessary features for ADA compliance
Updates

Designs look the same

Target Market(s)

US Federal Govt customers looking for IT support.

Industry/Entity Type

IT Consulting

Coding

Coded - Design and coding required

Colors
0054AA
0677BA
7BADD7
CADEEF
E8F1F8
0094D4
00A9DD
6FCCEA
C7EBF8
E9F6FB
00AB8E
00BBA5
67D7C9
C6EFE9
E9F9F6

```html
<!DOCTYPE html>
<html lang="en">
<head>
<meta charset="utf-8">
<title>Brisolux Federal Services — Federal IT Consulting</title>
<link href="https://fonts.googleapis.com/css2?family=Manrope:wght@400;500;600;700;800&display=swap" rel="stylesheet">
<style>
:root{
  --navy:#0054AA;
  --blue:#0677BA;
  --teal:#00BBA5;
  --teal-dark:#00AB8E;
  --ink:#111418;
  --body:#2a2f36;
  --mist:#F1F1F3;
  --white:#ffffff;
}
*{box-sizing:border-box;margin:0;padding:0}
html,body{width:1200px;height:3158px;overflow:hidden}
body{font-family:"Manrope",sans-serif;color:var(--ink);background:var(--white);position:relative}
.abs{position:absolute}
.btn{display:inline-block;border-radius:20px;font-weight:800;text-transform:uppercase;color:var(--white);text-decoration:none;text-align:center}
.btn-teal{background:var(--teal)}
.btn-navy{background:var(--navy)}

/* hero */
.hero{left:0;top:0;width:1200px;height:684px;background:linear-gradient(180deg,#2b2b2b 0%,#4a4540 45%,#2f2a26 100%)}
.hero-photo{position:absolute;inset:0;background:radial-gradient(ellipse at 55% 60%,#7a6a5c 0%,#3b3530 55%,#1f1c1a 100%)}
.brand{display:flex;align-items:center;gap:10px;color:var(--white);font-weight:800;letter-spacing:1px}
.brand-dot{width:34px;height:34px;border-radius:50%;background:var(--teal)}
.hero .brand{position:absolute;left:46px;top:30px;font-size:30px}
.nav{position:absolute;top:34px;right:62px;display:flex;gap:20px;font-size:17px}
.nav a{color:var(--white);text-decoration:none;padding:6px 14px;border-radius:16px}
.nav a.active{background:var(--blue)}
.hero h1{position:absolute;top:122px;left:0;width:1200px;text-align:center;color:var(--white);font-size:45px;font-weight:800}
.hero p{position:absolute;top:188px;left:0;width:1200px;text-align:center;color:var(--white);font-size:19px}
.hero .btn{position:absolute;left:529px;top:238px;width:142px;height:42px;line-height:42px;font-size:16px}

/* headings */
.section-title{left:0;width:1200px;text-align:center;font-size:32px;font-weight:800}
.rule{width:44px;height:4px;background:var(--navy)}

/* services */
.card{width:453px;height:234px;border-radius:4px;color:var(--white)}
.card.teal{background:var(--teal)}
.card.navy{background:var(--navy)}
.card .icon{position:absolute;left:34px;top:62px;width:104px;height:104px;border-radius:50%;background:rgba(255,255,255,.9)}
.card h3{position:absolute;left:169px;top:36px;width:250px;font-size:18px;font-weight:700;line-height:24px}
.card p{position:absolute;left:169px;top:98px;width:250px;font-size:12px;line-height:19px}
.card .btn{position:absolute;left:169px;top:173px;width:107px;height:31px;line-height:31px;font-size:12px}

/* welcome */
.welcome{left:0;top:1433px;width:1200px;height:537px;background:linear-gradient(120deg,var(--mist) 55%,#e6e7ea 75%,#f6f6f7 100%)}
.welcome h2{position:absolute;left:133px;top:54px;font-size:35px;line-height:44px;font-weight:800}
.welcome h2 .navy{color:var(--navy)}
.welcome h2 .teal{color:var(--teal)}
.welcome .rule{position:absolute;left:133px;top:210px}
.welcome p{position:absolute;left:133px;top:254px;width:430px;font-size:14px;line-height:21.6px;text-align:justify;color:var(--body)}
.welcome .btn{position:absolute;left:135px;top:438px;width:118px;height:36px;line-height:36px;font-size:14px}
.welcome-photo{position:absolute;left:655px;top:74px;width:394px;height:394px;border-radius:50%;border:22px solid var(--teal);background:linear-gradient(160deg,#e9e9e9,#a9a7a3 60%,#6b6560)}

/* testimonials */
.tcard{width:299px;height:320px;background:var(--white);border-radius:12px;box-shadow:0 4px 26px rgba(0,0,0,.08)}
.tcard .quote{position:absolute;left:36px;top:14px;font-size:64px;font-weight:700;color:var(--teal);font-family:"Manrope",sans-serif}
.tcard .stars{position:absolute;left:88px;top:44px;color:var(--teal);font-size:15px;letter-spacing:1px}
.tcard p{position:absolute;left:39px;top:94px;width:230px;font-size:13.5px;line-height:20.8px;color:var(--body)}
.tcard .tail{position:absolute;left:48px;bottom:-20px;width:0;height:0;border-left:12px solid transparent;border-right:12px solid transparent;border-top:20px solid var(--white)}
.person{display:flex;align-items:center;gap:17px}
.avatar{width:44px;height:44px;border-radius:50%;background:linear-gradient(#9aa2ab,#4b5158)}
.person strong{display:block;font-size:14px;font-weight:500}
.person span{font-size:12.5px;color:var(--body)}
.dots{left:552px;top:2623px;display:flex;gap:10px}
.dots i{width:11px;height:11px;border-radius:50%;background:#9a9ea3}
.dots i.on{background:var(--teal)}

/* consult */
.consult{left:131px;top:2716px;width:937px;height:131px;border-radius:12px;background:linear-gradient(90deg,#0a7f7a 0%,#0b4e6b 45%,#0c2a5e 75%,#0b2356 100%);overflow:hidden}
.consult h2{position:absolute;left:67px;top:50px;font-size:24px;font-weight:600;color:var(--white)}
.consult .btn{position:absolute;left:739px;top:47px;width:119px;height:34px;line-height:34px;font-size:13px}

/* footer */
.footer{left:0;top:2918px;width:1200px;height:240px;background:var(--navy);color:var(--white)}
.footer .brand{position:absolute;left:134px;top:46px;font-size:30px}
.fnav{position:absolute;right:132px;top:64px;display:flex;gap:44px;font-size:16px}
.fnav a{color:var(--white);text-decoration:none}
.fline{position:absolute;left:134px;top:127px;width:934px;height:1px;background:rgba(255,255,255,.35)}
.follow{position:absolute;left:135px;top:172px;display:flex;align-items:center;gap:8px;font-size:14px}
.follow span{margin-right:14px}
.follow i{width:28px;height:28px;border-radius:50%;background:var(--white);display:inline-block}
.copy{position:absolute;right:136px;top:172px;font-size:13px}
</style>
</head>
<body>

<header class="abs hero">
  <div class="hero-photo" role="img" aria-label="Photo of a consultant explaining to colleagues around a meeting table with a laptop"></div>
  <div class="brand"><span class="brand-dot"></span>BRISOLUX</div>
  <nav class="nav"><a class="active" href="#">Home</a><a href="#">Services</a><a href="#">About</a><a href="#">Contact</a></nav>
  <h1>FEDERAL IT CONSULTING</h1>
  <p>Expert guidance to navigate the federal IT landscape with ease and confidence.</p>
  <a class="btn btn-teal" href="#">Read More</a>
</header>

<h2 class="abs section-title" style="top:744px">OUR SERVICES</h2>
<div class="abs rule" style="left:578px;top:817px"></div>

<article class="abs card teal" style="left:133px;top:874px">
  <div class="icon" role="img" aria-label="Cloud computing icon"></div>
  <h3>Cloud Computing<br>Solutions</h3>
  <p>Lorem ipsum dolor sit amet, consectetur adipiscing elit, sed do eiusmod tempor incididunt ut labore et dolore .</p>
  <a class="btn btn-navy" href="#">Read More</a>
</article>
<article class="abs card navy" style="left:615px;top:874px">
  <div class="icon" role="img" aria-label="Cybersecurity icon"></div>
  <h3>Cybersecurity<br>Services</h3>
  <p>Lorem ipsum dolor sit amet, consectetur adipiscing elit, sed do eiusmod tempor incididunt ut labore et dolore .</p>
  <a class="btn btn-teal" href="#">Read More</a>
</article>
<article class="abs card navy" style="left:133px;top:1137px">
  <div class="icon" role="img" aria-label="Digital transformation icon"></div>
  <h3>Digital Transformation<br>and Modernization</h3>
  <p>Lorem ipsum dolor sit amet, consectetur adipiscing elit, sed do eiusmod tempor incididunt ut labore et dolore .</p>
  <a class="btn btn-teal" href="#">Read More</a>
</article>
<article class="abs card navy" style="left:615px;top:1137px">
  <div class="icon" role="img" aria-label="Data analytics icon"></div>
  <h3>Data Analytics and<br>Management</h3>
  <p>Lorem ipsum dolor sit amet, consectetur adipiscing elit, sed do eiusmod tempor incididunt ut labore et dolore .</p>
  <a class="btn btn-teal" href="#">Read More</a>
</article>

<section class="abs welcome">
  <h2>WELCOME TO<br><span class="navy">BRISOLUX FEDERAL</span><br><span class="teal">SERVICES</span></h2>
  <div class="rule"></div>
  <p>Sed ut perspiciatis unde omnis iste natus error sit voluptatem accusantium doloremque laudantium, totam rem aperiam, eaque ipsa quae ab illo inventore veritatis et quasi architecto beatae vitae dicta sunt explicabo. Nemo enim ipsam voluptatem quia voluptas sit aspernatur aut odit aut fugit, sed quia consequuntur magni dolores eos qui ratione voluptatem sequi nesciunt. Neque porro quisquam est, qui dolorem ipsum quia dolor sit ame.</p>
  <a class="btn btn-teal" href="#">Read More</a>
  <div class="welcome-photo" role="img" aria-label="Photo of two businessmen shaking hands over a laptop, framed in a teal ring"></div>
</section>

<h2 class="abs section-title" style="top:2033px">CLIENT TESTIMONIALS</h2>
<div class="abs rule" style="left:578px;top:2107px"></div>

<svg class="abs" style="left:60px;top:2310px" width="150" height="180" viewBox="0 0 150 180" fill="none" stroke="#d9dadd" stroke-width="1.5" aria-hidden="true">
  <circle cx="90" cy="90" r="82"/><circle cx="90" cy="90" r="68"/><circle cx="90" cy="90" r="54"/>
</svg>
<svg class="abs" style="left:950px;top:2118px" width="170" height="170" viewBox="0 0 170 170" fill="none" stroke="#d9dadd" stroke-width="1.5" aria-hidden="true">
  <circle cx="80" cy="85" r="80"/><circle cx="80" cy="85" r="66"/><circle cx="80" cy="85" r="52"/>
</svg>

<article class="abs tcard" style="left:132px;top:2163px">
  <span class="quote">“</span><span class="stars">★★★★★</span>
  <p>Sed ut perspiciatis unde omnis iste natus error sit voluptatem accusa ntium doloremque laudantium, totam rem aperiam, eaque ipsa quae ab illo inventore veritatis et quasi architecto beatae vitae dicta sunt explicabo. Nemo enim ipsam voluptatem quia voluptas sit aspernatur aut.</p>
  <span class="tail"></span>
</article>
<article class="abs tcard" style="left:451px;top:2163px">
  <span class="quote">“</span><span class="stars">★★★★★</span>
  <p>Sed ut perspiciatis unde omnis iste natus error sit voluptatem accusa ntium doloremque laudantium, totam rem aperiam, eaque ipsa quae ab illo inventore veritatis et quasi architecto beatae vitae dicta sunt explicabo. Nemo enim ipsam voluptatem quia voluptas sit aspernatur aut.</p>
  <span class="tail"></span>
</article>
<article class="abs tcard" style="left:770px;top:2163px">
  <span class="quote">“</span><span class="stars">★★★★★</span>
  <p>Sed ut perspiciatis unde omnis iste natus error sit voluptatem accusa ntium doloremque laudantium, totam rem aperiam, eaque ipsa quae ab illo inventore veritatis et quasi architecto beatae vitae dicta sunt explicabo. Nemo enim ipsam voluptatem quia voluptas sit aspernatur aut.</p>
  <span class="tail"></span>
</article>

<div class="abs person" style="left:146px;top:2508px"><div class="avatar" role="img" aria-label="Client portrait"></div><div><strong>Marcus Delaney</strong><span>Singapore</span></div></div>
<div class="abs person" style="left:466px;top:2508px"><div class="avatar" role="img" aria-label="Client portrait"></div><div><strong>Marcus Delaney</strong><span>Singapore</span></div></div>
<div class="abs person" style="left:784px;top:2508px"><div class="avatar" role="img" aria-label="Client portrait"></div><div><strong>Marcus Delaney</strong><span>Singapore</span></div></div>

<div class="abs dots"><i class="on"></i><i></i><i></i><i></i><i></i></div>

<section class="abs consult" role="img" aria-label="Banner with photo of hands typing on a laptop in teal and navy tones">
  <h2>BOOK A CONSULTATION</h2>
  <a class="btn btn-teal" href="#">Contact Us</a>
</section>

<footer class="abs footer">
  <div class="brand"><span class="brand-dot"></span>BRISOLUX</div>
  <nav class="fnav"><a href="#">Home</a><a href="#">Services</a><a href="#">About</a><a href="#">Contact</a></nav>
  <div class="fline"></div>
  <div class="follow"><span>Follow us</span><i aria-label="Social link 1"></i><i aria-label="Social link 2"></i><i aria-label="Social link 3"></i><i aria-label="Social link 4"></i></div>
  <div class="copy">Copyright © 2024 All Rights Reserved</div>
</footer>

</body>
</html>
```